Buch-/eBook-Cover für Traumatherapeutin
Zielgruppe
Ich bin Traumatherapeutin und schreibe ein Buch zum Thema Trauma bearbeiten.
Meine Zielgruppe sucht Heilung, Genesung, Selbstliebe etc.
Aufgabenstellung
Buchcover
Bitte erstell mir ein modernes positives inspirierendes Buchcover mit dem
Titel: 'Morgenlicht NEU entdecken“
Untertitel: „Spüre den Mut der ganz in dir wohnt“
Dr. Mira Kessow
Ich hätte gerne ein modernes Buch, das entweder einen Bezug zum Thema Trauma hat oder aber einfach stylische Schriftzüge. Bin aber auch offen für andere Vorschläge.
Dunkelblau, weiß und türkis oder auch rosa mag ich ganz gerne. Wobei Dunkelblau, weiß und türkis meine Favoriten sind und mit rosa höchstens kleinere Akzente gesetzt werden sollten.
Das Buchcover soll modern sein und direkt ansprechen. Gerne eine originelle Lösung, oder etwas Besonderes, etwas das Tiefe ausdrückt, oder man mehrmals hinsehen muss um etwas zu erkennen oder etwas das mehr Interpretationsspielraum lässt.
Gerne auch viel weiß, zumindest heller und nicht zu dunkel. Stylish, aber nicht überfrachtet.
Schreib mich gerne an, wenn du Fragen hast.
Ich habe mal zwei Beispiel von Typolösungen angehängt, die ich ganz cool fände.
Ich freue mich auf deine Ideen :-)
Ganz liebe Grüße
Mira

```html
<!DOCTYPE html>
<html lang="de">
<head>
<meta charset="utf-8">
<title>Morgenlicht neu entdecken – Dr. Mira Kessow</title>
<link rel="stylesheet" href="https://fonts.googleapis.com/css2?family=Archivo+Black&family=Great+Vibes&family=Jost:wght@400;500&display=swap">
<style>
  :root {
    --sky-blue: #3aa8c6;
    --sky-blue-light: #5fbfd8;
    --sky-blue-deep: #2e93b2;
    --teal: #6ab3b8;
    --teal-edge: #5aa3a6;
    --white: #ffffff;
    --navy: #1f4f7a;
    --ice: #e6f4f7;
    --rose: #e7879f;
  }
  html, body {
    margin: 0;
    padding: 0;
    width: 848px;
    height: 1200px;
    overflow: hidden;
    background: var(--teal);
  }
  .cover {
    position: relative;
    width: 848px;
    height: 1200px;
    background: var(--teal);
    overflow: hidden;
  }
  .cover__texture {
    position: absolute;
    left: 0;
    top: 0;
    width: 848px;
    height: 590px;
    background:
      radial-gradient(ellipse 260px 180px at 230px 170px, var(--sky-blue-light) 0%, transparent 70%),
      radial-gradient(ellipse 200px 140px at 620px 120px, rgba(95,191,216,0.6) 0%, transparent 70%),
      linear-gradient(180deg, var(--sky-blue) 0%, var(--sky-blue-deep) 100%);
    border-bottom: 4px solid var(--teal-edge);
  }
  .cover__title {
    position: absolute;
    left: 0;
    top: 520px;
    width: 848px;
    height: 160px;
  }
  .cover__script {
    position: absolute;
    left: 0;
    top: 640px;
    width: 848px;
    height: 220px;
  }
  .cover__script text {
    font-family: "Great Vibes", cursive;
    fill: var(--white);
  }
  .cover__subtitle {
    position: absolute;
    left: 314px;
    top: 944px;
    width: 440px;
    margin: 0;
    font-family: "Jost", sans-serif;
    font-weight: 500;
    font-size: 20.5px;
    line-height: 38px;
    letter-spacing: 0.3px;
    color: var(--white);
    text-transform: uppercase;
  }
  .cover__subtitle span { display: block; }
  .cover__subtitle .line-2 { text-align: right; }
  .cover__author {
    position: absolute;
    left: 312px;
    top: 1066px;
    margin: 0;
    font-family: "Jost", sans-serif;
    font-weight: 500;
    font-size: 46px;
    line-height: 1;
    letter-spacing: 0.5px;
    color: var(--white);
    text-transform: uppercase;
  }
</style>
</head>
<body>
<main class="cover">
  <div class="cover__texture" role="img" aria-label="Gemalte türkisblaue Leinwandstruktur mit hellen Pinselspuren"></div>

  <svg class="cover__title" viewBox="0 0 848 160" aria-label="Morgenlicht">
    <defs>
      <linearGradient id="title-fill" x1="0" y1="0" x2="1" y2="0">
        <stop offset="0" stop-color="var(--navy)"/>
        <stop offset="0.4" stop-color="#2f6f9c"/>
        <stop offset="0.7" stop-color="var(--ice)"/>
        <stop offset="0.9" stop-color="var(--ice)"/>
        <stop offset="1" stop-color="var(--rose)"/>
      </linearGradient>
      <filter id="title-shadow" x="-5%" y="-20%" width="110%" height="150%">
        <feDropShadow dx="4" dy="6" stdDeviation="3" flood-color="#2a6d72" flood-opacity="0.45"/>
      </filter>
    </defs>
    <text x="24" y="133" font-family="'Archivo Black', sans-serif" font-size="150"
          textLength="776" lengthAdjust="spacingAndGlyphs"
          fill="url(#title-fill)" filter="url(#title-shadow)">MORGENLICHT</text>
  </svg>

  <svg class="cover__script" viewBox="0 0 848 220" aria-label="… neu entdecken!">
    <text x="208" y="102" font-size="120">… neu</text>
    <text x="306" y="174" font-size="124">entdecken!</text>
  </svg>

  <p class="cover__subtitle">
    <span class="line-1">Spüre den Mut,</span>
    <span class="line-2">der ganz in dir wohnt!</span>
  </p>

  <p class="cover__author">Dr. Mira Kessow</p>
</main>
</body>
</html>
```